KAJU Freightways #ALLKAJU Business Cards & Letterhead

I am looking to business cards designed for our organization. We are currently undergoing a small re-branding that is taking place. Our organization is called KAJU Freightways and we are headquartered in Phoenix, AZ. We primarily provide transportation and logistics services to the Marlow Parcel Bureau who is our largest customer. I would like to see a design that incorporates name, title, contact info, website, and address (this will be different depending on the employee). I would also like to see some color on the business card using our logo colors or a variation. I would like our logo on the back of the business card with the website displayed. The final design should communicate that we are a next generation transportation operate that focuses on being driver-first, customer-centric, innovative, and sustainable.We would also like our #ALLKAJU catch phrase incorporated as well.

Target Market(s)

Transportation & Logistics

Industry/Entity Type

Trucking Company

Contact Information for Business Card

-First and Last Name
-Position Title
-Contact Phone
-Contact Email
-Physical Address

Font styles to use
Serif

Colors

Designer to choose colors to be used in the design.

Requirements
Must have
• -KAJU logo prominently displayed
• -#ALLKAJU catch phrase used
• -Some amount of color, design gradient, etc.
• -Logo on the back with website listed (https://www.kajufreightco.example)

```html
<!DOCTYPE html>
<html lang="en">
<head>
<meta charset="utf-8">
<title>KAJU Freightways Business Card</title>
<link href="https://fonts.googleapis.com/css2?family=Roboto+Serif:opsz,wght@8..144,400;8..144,700;8..144,900&family=Roboto+Slab:wght@700&display=swap" rel="stylesheet">
<style>
  :root {
    --backdrop: #e0e0de;
    --paper: #fafafa;
    --ink: #0d3b4a;
    --lime: #7dc42a;
    --white: #ffffff;
    --grad-top: #0e4a55;
    --grad-mid: #3f7d58;
    --grad-bottom: #7cc02c;
  }
  * { margin: 0; padding: 0; box-sizing: border-box; }
  html, body { width: 1200px; height: 828px; overflow: hidden; }
  body {
    background: var(--backdrop);
    position: relative;
    font-family: "Roboto Serif", Georgia, serif;
  }
  .card {
    position: absolute;
    top: 102px;
    width: 377px;
    height: 623px;
    overflow: hidden;
  }
  .card-back { left: 194px; }
  .card-front { left: 628px; background: var(--paper); text-align: center; color: var(--ink); }

  .back-photo {
    position: absolute; inset: 0;
    background: linear-gradient(200deg, var(--grad-top) 0%, var(--grad-mid) 50%, #5f9a4c 80%, var(--grad-bottom) 100%);
  }
  .logo-mark {
    position: absolute;
    display: flex; align-items: center; justify-content: center;
    border-radius: 50%;
    font-family: "Roboto Serif", Georgia, serif;
    font-weight: 900;
    letter-spacing: 1px;
  }
  .card-back .logo-mark {
    left: 76px; top: 176px;
    width: 226px; height: 226px;
    border: 5px solid var(--white);
    color: var(--white);
    font-size: 60px;
  }
  .back-tagline {
    position: absolute; left: 0; right: 0; top: 540px;
    text-align: center;
    color: var(--white);
    font-weight: 700;
    font-size: 16px;
    letter-spacing: 3px;
  }
  .back-website {
    position: absolute; left: 0; right: 0; top: 578px;
    text-align: center;
    color: var(--white);
    font-size: 14px;
    letter-spacing: 3.6px;
  }
  .card-front .logo-mark {
    left: 74px; top: 53px;
    width: 228px; height: 228px;
    border: 5.5px solid var(--lime);
    color: var(--ink);
    font-size: 62px;
  }
  .person-name {
    position: absolute; left: 0; right: 0; top: 322px;
    font-family: "Roboto Slab", Georgia, serif;
    font-weight: 700; font-size: 26px;
  }
  .person-title {
    position: absolute; left: 0; right: 0; top: 356px;
    color: var(--lime); font-size: 15px;
  }
  .contact-divider {
    position: absolute; left: 85px; top: 405px;
    width: 207px; height: 16px;
  }
  .contact-list {
    position: absolute; left: 0; right: 0; top: 437px;
    list-style: none; font-size: 15px; line-height: 24px;
  }
  .company-name {
    position: absolute; left: 0; right: 0; top: 518px;
    color: var(--lime); font-weight: 700; font-size: 14.5px;
  }
  .company-address {
    position: absolute; left: 0; right: 0; top: 542px;
    font-style: normal; font-size: 15px; line-height: 24px;
  }
</style>
</head>
<body>
  <section class="card card-back">
    <div class="back-photo" role="img" aria-label="Photo of a white freight truck cab under a teal-to-green gradient"></div>
    <div class="logo-mark">KAJU</div>
    <p class="back-tagline">#ALLKAJU</p>
    <p class="back-website">www.kajufreightco.example</p>
  </section>

  <section class="card card-front">
    <div class="logo-mark">KAJU</div>
    <h1 class="person-name">Marcus Delane</h1>
    <p class="person-title">Chairman &amp; CEO</p>

    <svg class="contact-divider" viewBox="0 0 207 16" aria-hidden="true">
      <line x1="0" y1="8" x2="55" y2="8" stroke="#7dc42a" stroke-width="1.2"/>
      <line x1="152" y1="8" x2="207" y2="8" stroke="#7dc42a" stroke-width="1.2"/>
      <g fill="#7dc42a">
        <path d="M72 5 q7 -4 14 0 v3 h-3 v-1.5 q-4 -1.5 -8 0 v1.5 h-3z"/>
        <rect x="74" y="8" width="10" height="6" rx="1"/>
      </g>
      <g>
        <rect x="96" y="4" width="14" height="10" fill="#7dc42a"/>
        <path d="M96 4 l7 6 l7 -6 M96 14 l5 -5 M110 14 l-5 -5" stroke="#fafafa" stroke-width="1" fill="none"/>
      </g>
      <g fill="none" stroke="#7dc42a" stroke-width="1.3">
        <circle cx="128" cy="9" r="6"/>
        <ellipse cx="128" cy="9" rx="2.6" ry="6"/>
        <line x1="122" y1="9" x2="134" y2="9"/>
      </g>
    </svg>

    <ul class="contact-list">
      <li>623-555-0148</li>
      <li>marcus@kajufreightco.example</li>
      <li>www.kajufreightco.example</li>
    </ul>

    <p class="company-name">KAJU Freightways &amp; Energy Services</p>
    <address class="company-address">4170 North Desert Ridge<br>Parkway Glendale, AZ 85308</address>
  </section>
</body>
</html>
```